Business Card Design for Software Development Company

I am looking for a business card design the incorporates my new logo (attached below).

Key information to include:
Name: Martin Quelbrook
Title: CEO
Email: martin@brightwellcivic.example
Phone: 555-218-9403
Website: www.brightwellcivic.example

NOTE: This design should be easy to edit so that we can order cards for different members of our team.

```html
<!DOCTYPE html>
<html lang="en">
<head>
<meta charset="utf-8">
<title>BrightwellLabs Business Card</title>
<link rel="stylesheet" href="https://fonts.googleapis.com/css2?family=Montserrat:wght@400;500;700&display=swap">
<style>
  :root {
    --backdrop: #2b2b2d;
    --card-white: #ffffff;
    --card-slate: #6e7599;
    --ink-navy: #2c3150;
    --ink-body: #2a2a2a;
    --accent-orange: #e8792f;
    --type: "Montserrat", sans-serif;
  }
  * { margin: 0; padding: 0; box-sizing: border-box; }
  html, body {
    width: 1200px; height: 875px; overflow: hidden;
    background: var(--backdrop);
    font-family: var(--type);
  }
  .canvas {
    position: relative; width: 1200px; height: 875px;
  }
  .card {
    position: absolute; left: 320px; width: 560px; height: 320px;
    border-radius: 22px; overflow: hidden;
  }
  /* Reverse side */
  .card--back { top: 90px; background: var(--card-slate); }
  .back-brand {
    position: absolute; left: 44px; bottom: 48px;
    color: var(--card-white);
  }
  .back-brand__name {
    font-weight: 700; font-size: 66px; letter-spacing: -1px; line-height: 1;
  }
  .back-brand__tagline {
    font-weight: 500; font-size: 7px; letter-spacing: 1px;
    text-transform: uppercase; text-align: right; margin-top: 6px;
  }
  /* Front side */
  .card--front { top: 465px; background: var(--card-white); }
  .front-brand {
    position: absolute; left: 40px; top: 142px; color: var(--ink-navy);
  }
  .front-brand__name {
    font-weight: 700; font-size: 30px; letter-spacing: -0.5px; line-height: 1;
  }
  .front-brand__tagline {
    font-weight: 500; font-size: 4.5px; letter-spacing: 0.6px;
    text-transform: uppercase; text-align: right; margin-top: 3px;
  }
  .divider {
    position: absolute; left: 282px; top: 88px; width: 1.5px; height: 150px;
    background: var(--accent-orange);
  }
  .contact {
    position: absolute; left: 302px; top: 92px;
  }
  .contact__name {
    font-weight: 700; font-size: 26px; color: var(--accent-orange); line-height: 1.1;
  }
  .contact__title {
    font-weight: 500; font-size: 14px; color: var(--ink-body); margin: 2px 0 10px;
  }
  .contact__list { list-style: none; }
  .contact__item {
    display: flex; align-items: center; gap: 8px;
    font-size: 13px; color: var(--ink-body); line-height: 1.75;
  }
  .contact__icon { width: 11px; height: 11px; flex: none; fill: var(--accent-orange); }
</style>
</head>
<body>
<main class="canvas">
  <section class="card card--back" aria-label="Card reverse">
    <div class="back-brand">
      <div class="back-brand__name">BrightwellLabs</div>
      <div class="back-brand__tagline">A Division of Brightwell Civic</div>
    </div>
  </section>

  <section class="card card--front" aria-label="Card front">
    <div class="front-brand">
      <div class="front-brand__name">BrightwellLabs</div>
      <div class="front-brand__tagline">A Division of Brightwell Civic</div>
    </div>
    <div class="divider"></div>
    <div class="contact">
      <div class="contact__name">Martin Quelbrook</div>
      <div class="contact__title">CEO</div>
      <ul class="contact__list">
        <li class="contact__item">
          <svg class="contact__icon" viewBox="0 0 24 24" aria-hidden="true"><path d="M6.6 10.8a15.5 15.5 0 0 0 6.6 6.6l2.2-2.2c.3-.3.7-.4 1-.2 1.1.4 2.3.6 3.6.6.6 0 1 .4 1 1V20c0 .6-.4 1-1 1A17 17 0 0 1 3 4c0-.6.4-1 1-1h3.5c.6 0 1 .4 1 1 0 1.3.2 2.5.6 3.6.1.3 0 .7-.2 1z"/></svg>
          <span>555-218-9403</span>
        </li>
        <li class="contact__item">
          <svg class="contact__icon" viewBox="0 0 24 24" aria-hidden="true"><path d="M2 5h20v14H2z M2 5l10 8 10-8" fill="var(--accent-orange)"/><path d="M3 6l9 7 9-7" fill="none" stroke="#fff" stroke-width="1.6"/></svg>
          <span>martin@brightwellcivic.example</span>
        </li>
        <li class="contact__item">
          <svg class="contact__icon" viewBox="0 0 24 24" aria-hidden="true"><circle cx="12" cy="12" r="10"/><path d="M2 12h20M12 2c3 3 3 17 0 20M12 2c-3 3-3 17 0 20" fill="none" stroke="#fff" stroke-width="1.4"/></svg>
          <span>www.brightwellcivic.example</span>
        </li>
      </ul>
    </div>
  </section>
</main>
</body>
</html>
```